Reach Crafters Unique Marketing Website Design

I am starting a new company that is a thought leader in the marketing consulting space. The company is called Reach Crafters. We intend to build a Wordpress site on the Astra Theme with the Spectra builder. Our goal is to become the leading voice that empowers high-ticket service business leaders to become Reach Crafters by equipping them with the cutting-edge frameworks and decision grade intelligence taught in leading business schools. What we are looking for is a website design that is clean and professional, making some use of white space well also being eye catching and distinctive in the consulting space. We will probably want to have a video on the homepage not in the hero section, but just below to explain the company and what we do. Our tagline is "Be found. Be chosen." I have attached a brand guide with some messaging, our typography choices, and our color system. The full site will have a primary nav that is four pages - About us, Services, Insights (essentially a blog), and Contact Us. The goal of this project is to develop an art direction that I can give to a designer to build loads of new pages.

Target Market(s)

Business owners (mostly male) from 30-60 years old, looking to fix their sales and marketing funnel.

Industry/Entity Type

Marketing consulting

Font styles to use
Sans Serif

Requirements
Must have
• A clean, professional design that builds trust with owners of high-ticket service businesses. We need a space for explainer video, and sections that tell prospects what we do. Would also like to have a blog carousel.
Nice to have
• Social feeds, if possible. See attached documents for colors and fonts.
Should not have
• Our feel is professional enough to be trustworthy, but unique enough to be memorable. Cartoon ideas do not meet the professional test, and we do not want the website to appear feminine.

```html
<!DOCTYPE html>
<html lang="en">
<head>
<meta charset="utf-8">
<title>Reach Crafters — Be Found. Be Chosen.</title>
<link rel="stylesheet" href="https://fonts.googleapis.com/css2?family=Oswald:wght@300;400;500;600&family=Inter:wght@400;500;600;700&display=swap">
<style>
:root{
  --blue:#1f3bf0;
  --ink:#1c1c22;
  --text:#3a3a44;
  --muted:#6b6b76;
  --line:#d9d9df;
  --tint:#eef0fb;
  --grey:#f2f2f3;
  --white:#fff;
}
*{box-sizing:border-box;margin:0;padding:0}
html,body{width:1200px;height:4946px;overflow:hidden}
body{font-family:"Inter",sans-serif;color:var(--text);background:var(--white);position:relative}
.abs{position:absolute}
.display{font-family:"Oswald",sans-serif;font-weight:400;color:var(--ink);text-transform:uppercase;letter-spacing:-.5px}
.display b{font-weight:600;color:var(--blue)}
.btn{position:absolute;display:flex;align-items:center;justify-content:center;border-radius:30px;font-weight:600;font-size:14px;text-transform:uppercase;letter-spacing:.3px}
.btn-blue{background:var(--blue);color:#fff}
.btn-white{background:#fff;color:var(--blue)}
.wordmark{font-family:"Inter",sans-serif;font-weight:700;color:var(--ink);text-transform:uppercase;letter-spacing:.2px}
.photo{position:absolute;overflow:hidden}

/* header */
.site-header{position:absolute;top:0;left:0;width:1200px;height:85px;background:#fff}
.site-header .wordmark{left:90px;top:22px;font-size:30px}
.nav{position:absolute;top:35px;font-size:13px;color:var(--ink);text-transform:uppercase}
.nav.active{color:var(--blue)}
.call-box{position:absolute;left:955px;top:0;width:245px;height:85px;background:var(--blue);color:#fff}
.call-box small{position:absolute;left:50px;top:24px;font-size:9px;font-weight:700}
.call-box strong{position:absolute;left:50px;top:36px;font-size:22px;font-weight:700}
.call-icon{position:absolute;left:933px;top:17px;width:52px;height:52px;border-radius:50%;background:var(--blue);border:3px solid #fff;display:flex;align-items:center;justify-content:center}

/* hero */
.hero{position:absolute;top:85px;left:0;width:1200px;height:700px}
.hero-frame{position:absolute;left:245px;top:135px;width:712px;height:180px;border:2px solid rgba(255,255,255,.85);border-bottom:none}
.hero h1{position:absolute;left:0;width:1200px;top:176px;text-align:center;font-family:"Oswald",sans-serif;font-weight:300;color:#fff;font-size:66px;line-height:72px;text-transform:uppercase;letter-spacing:-.5px}
.hero h1 b{font-weight:600}
.hero p{position:absolute;left:0;width:1200px;top:342px;text-align:center;color:#fff;font-size:15px;font-weight:600;line-height:26px}
.dots{position:absolute;top:585px;left:565px;display:flex;gap:6px;align-items:center}
.dots i{width:8px;height:8px;border-radius:50%;background:#fff;display:block}
.dots i.on{width:12px;height:12px;border:2px solid var(--blue);box-shadow:0 0 0 2px #fff}

/* about */
.about-main{left:106px;top:890px;width:440px;height:440px;border-radius:50%;
  background:
    radial-gradient(circle at 68% 38%,#e3b07a 0,#c8793f 22%,transparent 46%),
    radial-gradient(circle at 25% 70%,#3c3a38 0,transparent 40%),
    linear-gradient(135deg,#6e5a44,#a88b6a 40%,#e2dccf 80%);
  box-shadow:0 10px 30px rgba(0,0,0,.18)}
.about-small{left:342px;top:1144px;width:238px;height:238px;border-radius:50%;
  background:
    radial-gradient(circle at 35% 40%,#c79b82 0,transparent 30%),
    radial-gradient(circle at 70% 45%,#9a7c6a 0,transparent 28%),
    linear-gradient(160deg,#7d828c,#d8d5cf 55%,#4d5159);
  border:5px solid #fff;box-shadow:0 8px 22px rgba(0,0,0,.2)}
.play{left:296px;top:1082px;width:60px;height:56px;border-radius:50%;background:#e8141b;display:flex;align-items:center;justify-content:center}
.about-title{left:670px;top:936px;font-size:46px;line-height:60px}
.about-copy{left:671px;top:1003px;width:418px;font-size:13px;line-height:26px;color:var(--muted);text-align:justify}
.about-copy p+p{margin-top:26px}

/* services */
.services{position:absolute;top:1503px;left:0;width:1200px;height:782px;background:linear-gradient(180deg,var(--tint),#fff 85%)}
.sec-title{position:absolute;left:0;width:1200px;text-align:center;font-size:46px;line-height:60px}
.services .lead{position:absolute;left:0;width:1200px;top:152px;text-align:center;font-size:15px;line-height:26px;color:var(--ink)}
.card{position:absolute;top:246px;width:298px;height:468px;background:#fff;border:1px solid var(--line);border-radius:18px;overflow:hidden;text-align:center}
.card .photo{position:relative;height:292px}
.card h3{margin-top:18px;font-size:20px;font-weight:700;color:var(--ink)}
.card p{margin:10px auto 0;width:266px;font-size:14px;line-height:26px;color:var(--text)}

/* be found */
.found{position:absolute;top:2285px;left:0;width:1200px;height:1065px}
.found h2{position:absolute;left:0;width:1200px;top:612px;text-align:center;font-family:"Oswald",sans-serif;font-weight:300;color:#fff;font-size:44px;line-height:60px;text-transform:uppercase}
.found h2 b{font-weight:600}
.found p{position:absolute;left:205px;width:790px;text-align:center;color:#fff;font-size:16.5px;line-height:32px}

/* news */
.news-title{top:3425px}
.post{position:absolute;top:3510px;width:300px}
.post .photo{position:relative;height:219px}
.post h4{margin-top:18px;font-size:16px;font-weight:400;line-height:28px;color:var(--ink)}
.post time{display:block;margin-top:8px;font-size:11px;color:var(--blue)}
.post a{display:block;margin-top:10px;font-size:12px;color:var(--muted);text-decoration:underline}
.arrow{position:absolute;top:3657px;width:40px;height:40px}

/* gallery */
.gallery{position:absolute;top:3936px;left:0;width:1200px;height:595px;background:var(--grey)}
.g{position:absolute;border-radius:22px}

/* footer */
.footer .wordmark{position:absolute;left:104px;top:4612px;font-size:34px}
.fcol{position:absolute;top:4640px}
.fcol h5{font-family:"Oswald",sans-serif;font-weight:500;font-size:15px;color:var(--ink);text-transform:uppercase}
.fcol ul{list-style:none;margin-top:14px;margin-left:8px}
.fcol li{font-size:13.5px;color:var(--ink);height:34.5px}
.contact-row{display:flex;gap:14px;align-items:flex-start;font-size:13.5px;color:var(--ink);line-height:26px}
.contact-row svg{flex:none}
.rule{position:absolute;left:111px;top:4863px;width:978px;height:1px;background:var(--line)}
.copy{position:absolute;left:0;width:1200px;top:4899px;text-align:center;font-size:13.5px;color:var(--ink)}
</style>
</head>
<body>

<header class="site-header">
  <div class="abs wordmark">Reach Crafters</div>
  <span class="nav active" style="left:430px">Home</span>
  <span class="nav" style="left:507px">About</span>
  <span class="nav" style="left:589px">Services</span>
  <span class="nav" style="left:689px">Insights</span>
  <span class="nav" style="left:787px">Contact</span>
  <div class="call-box"><small>CALL US</small><strong>+1 888 888 8888</strong></div>
  <div class="call-icon"><svg width="24" height="24" viewBox="0 0 24 24"><path fill="#fff" d="M6.6 10.8a15 15 0 0 0 6.6 6.6l2.2-2.2c.3-.3.7-.4 1-.2 1.1.4 2.3.6 3.6.6.6 0 1 .4 1 1V20c0 .6-.4 1-1 1A17 17 0 0 1 3 4c0-.6.4-1 1-1h3.5c.6 0 1 .4 1 1 0 1.3.2 2.5.6 3.6.1.3 0 .7-.2 1z"/></svg></div>
</header>

<section class="hero">
  <svg class="abs" style="left:0;top:0" width="1200" height="700" viewBox="0 0 1200 700">
    <defs>
      <linearGradient id="heroTone" x1="0" y1="0" x2="1" y2="1">
        <stop offset="0" stop-color="#6a7488"/><stop offset=".35" stop-color="#48526a"/><stop offset=".7" stop-color="#3a4256"/><stop offset="1" stop-color="#727a8c"/>
      </linearGradient>
      <radialGradient id="heroGlow" cx=".5" cy=".45" r=".55">
        <stop offset="0" stop-color="#8a93a6" stop-opacity=".55"/><stop offset="1" stop-color="#8a93a6" stop-opacity="0"/>
      </radialGradient>
    </defs>
    <g role="img" aria-label="Business team meeting around a table with charts and laptops">
      <path d="M0 0H1200V515Q600 755 0 525Z" fill="url(#heroTone)"/>
      <path d="M0 0H1200V515Q600 755 0 525Z" fill="url(#heroGlow)"/>
      <path d="M0 0H1200V515Q600 755 0 525Z" fill="#1c2234" opacity=".25"/>
    </g>
    <path d="M0 532Q600 870 1200 515Q600 768 0 532Z" fill="var(--blue)"/>
  </svg>
  <div class="hero-frame"></div>
  <h1>Become the demand your<br>market <b>can’t ignore</b></h1>
  <p>We equip high-ticket service leaders with the frameworks and<br>decision-grade intelligence used in top business schools.</p>
  <div class="btn btn-blue" style="left:523px;top:422px;width:152px;height:46px;border:2px solid #fff">Get Started</div>
  <div class="dots"><i></i><i></i><i class="on"></i><i></i><i></i></div>
</section>

<section class="about">
  <div class="photo about-main" role="img" aria-label="Consultant with headset working at a laptop in an office"></div>
  <div class="photo about-small" role="img" aria-label="Team of colleagues reviewing work on a laptop"></div>
  <div class="abs play"><svg width="20" height="22" viewBox="0 0 20 22"><path d="M2 1l17 10L2 21z" fill="#fff"/></svg></div>
  <h2 class="abs display about-title">About Reach <b>Crafters</b></h2>
  <div class="abs about-copy">
    <p>Reach Crafters exists to equip high-ticket service leaders with the strategic clarity, frameworks, and decision-grade intelligence needed to become the most desirable choice in their market.</p>
    <p>We combine the analytical rigor of leading business schools with the practical experience of operators who have built, scaled, and advised service businesses across multiple industries. Our work goes far beyond traditional marketing. We help leadership teams understand the true drivers of demand, architect a strategy that earns market preference, and execute with precision.</p>
  </div>
  <div class="btn btn-blue" style="left:671px;top:1272px;width:132px;height:50px">Read More</div>
</section>

<section class="services">
  <h2 class="display sec-title" style="top:76px">Our <b>Services</b></h2>
  <p class="lead">We’ll help you communicate your value clearly, create demand predictably, and become the first<br>call—not the fallback option.</p>
  <article class="card" style="left:110px">
    <div class="photo" role="img" aria-label="City buildings overlaid with healthcare technology icons" style="background:radial-gradient(circle at 65% 35%,#d6e6ef 0,transparent 45%),radial-gradient(circle at 70% 85%,#41c6e8 0,transparent 30%),linear-gradient(160deg,#a9c1d0,#5d8aa3 55%,#2f566e)"></div>
    <h3>Reach Diagnostic</h3>
    <p>The Reach Diagnostic™ is our foundational strategic analysis designed to uncover the true drivers of your growth.</p>
  </article>
  <article class="card" style="left:451px">
    <div class="photo" role="img" aria-label="Tall buildings with a rising orange growth arrow" style="background:radial-gradient(circle at 45% 40%,#e07a3c 0,transparent 22%),radial-gradient(ellipse at 65% 70%,#6f6357 0,transparent 45%),linear-gradient(180deg,#f4f1ec,#c8b49d 50%,#3b352f)"></div>
    <h3>Reach Architecture</h3>
    <p>The Reach Diagnostic™ is our foundational strategic analysis designed to uncover the true drivers of your growth.</p>
  </article>
  <article class="card" style="left:791px">
    <div class="photo" role="img" aria-label="Hand holding a phone with glowing network icons" style="background:radial-gradient(circle at 50% 45%,#6cc4ff 0,#2a7fd8 20%,#0f3b80 55%,#06142f)"></div>
    <h3>Reach Systems</h3>
    <p>The Reach Diagnostic™ is our foundational strategic analysis designed to uncover the true drivers of your growth.</p>
  </article>
</section>

<section class="found">
  <svg class="abs" style="left:0;top:0" width="1200" height="1065" viewBox="0 0 1200 1065">
    <defs>
      <linearGradient id="presentTone" x1="0" y1="0" x2="1" y2="0">
        <stop offset="0" stop-color="#cadbe6"/><stop offset=".3" stop-color="#dfe8ee"/><stop offset=".5" stop-color="#cfa583"/><stop offset=".62" stop-color="#e9e7e3"/><stop offset="1" stop-color="#eef1f4"/>
      </linearGradient>
      <linearGradient id="presentShade" x1="0" y1="0" x2="0" y2="1">
        <stop offset="0" stop-color="#fff" stop-opacity=".35"/><stop offset="1" stop-color="#5a4c42" stop-opacity=".25"/>
      </linearGradient>
    </defs>
    <g role="img" aria-label="Presenter showing charts on a screen to seated colleagues">
      <rect width="1200" height="560" fill="url(#presentTone)"/>
      <rect width="1200" height="560" fill="url(#presentShade)"/>
    </g>
    <path d="M0 365Q600 725 1200 365L1200 864Q600 1266 0 864Z" fill="var(--blue)"/>
  </svg>
  <h2>Be found. <b>Be chosen.</b></h2>
  <p style="top:685px">We help high-ticket service leaders create market demand through proven strategy, decision-grade intelligence, and smart execution. We equip service-based businesses with the frameworks and insights needed to attract better clients and accelerate growth.</p>
  <p style="top:812px">We combine academic-level frameworks with operator-level practicality to build demand—not noise. Consultants, professional firms, and specialized B2B service providers who sell expertise, not commodities.</p>
  <div class="btn btn-white" style="left:527px;top:956px;width:145px;height:46px;font-weight:500">Contact Us</div>
</section>

<section class="news">
  <h2 class="display sec-title news-title">Latest <b>News</b></h2>
  <svg class="arrow" style="left:34px" viewBox="0 0 40 40"><circle cx="20" cy="20" r="18" fill="none" stroke="#222" stroke-width="2"/><path d="M28 20H12m6-6-6 6 6 6" fill="none" stroke="#222" stroke-width="2"/></svg>
  <svg class="arrow" style="left:1125px" viewBox="0 0 40 40"><circle cx="20" cy="20" r="18" fill="none" stroke="#222" stroke-width="2"/><path d="M12 20h16m-6-6 6 6-6 6" fill="none" stroke="#222" stroke-width="2"/></svg>
  <article class="post" style="left:111px">
    <div class="photo" role="img" aria-label="Two colleagues smiling while reviewing notes" style="background:radial-gradient(circle at 40% 55%,#8b6a4c 0,transparent 35%),radial-gradient(circle at 75% 60%,#a7c3de 0,transparent 30%),linear-gradient(135deg,#ece7df,#b9a083 55%,#6f7580)"></div>
    <h4>Sed do eiusmod tempor incididunt<br>ut labore et dolore magna aliqua</h4>
    <time>September 13, 2025</time><a>Read More</a>
  </article>
  <article class="post" style="left:451px">
    <div class="photo" role="img" aria-label="Business people discussing around a desk" style="background:radial-gradient(circle at 60% 45%,#c9a58f 0,transparent 28%),linear-gradient(135deg,#cfd5da,#6b727c 50%,#262a32)"></div>
    <h4>Duis aute irure dolor in reprehenderit<br>in voluptate velit</h4>
    <time>September 13, 2025</time><a>Read More</a>
  </article>
  <article class="post" style="left:789px">
    <div class="photo" role="img" aria-label="Team collaborating in a bright office" style="background:radial-gradient(circle at 70% 60%,#2d3f63 0,transparent 32%),radial-gradient(circle at 35% 60%,#b88f73 0,transparent 28%),linear-gradient(135deg,#f1f3f5,#c0c8d2 55%,#6d7888)"></div>
    <h4>Excepteur sint occaecat cupidatat non<br>proident, sunt in culpa qui</h4>
    <time>August 13, 2025</time><a>Read More</a>
  </article>
</section>

<section class="gallery">
  <h2 class="display sec-title" style="top:80px">Our <b>Gallery</b></h2>
  <div class="g" role="img" aria-label="Hand touching a digital checklist interface" style="left:111px;top:163px;width:299px;height:198px;background:radial-gradient(circle at 40% 45%,#e6eefb 0,transparent 30%),radial-gradient(circle at 85% 30%,#c99a7c 0,transparent 28%),linear-gradient(135deg,#a8bde0,#4565a3 60%,#24396b)"></div>
  <div class="g" role="img" aria-label="Colleagues working together at a laptop" style="left:111px;top:376px;width:299px;height:135px;background:radial-gradient(circle at 30% 50%,#9b7a63 0,transparent 30%),radial-gradient(circle at 75% 50%,#8a6d5c 0,transparent 28%),linear-gradient(135deg,#c8ced5,#5b544e 55%,#2b2e35)"></div>
  <div class="g" role="img" aria-label="Support team members wearing headsets" style="left:420px;top:163px;width:358px;height:348px;background:radial-gradient(circle at 40% 40%,#d9b08d 0,transparent 30%),radial-gradient(circle at 55% 80%,#f1ede7 0,transparent 30%),linear-gradient(135deg,#e0d9ce,#a98566 50%,#48505c)"></div>
  <div class="g" role="img" aria-label="Hands pointing at charts and a tablet" style="left:789px;top:163px;width:299px;height:348px;background:radial-gradient(circle at 55% 65%,#c8d6e6 0,transparent 30%),radial-gradient(circle at 65% 25%,#2a2f38 0,transparent 30%),linear-gradient(135deg,#6b7480,#b8c2cc 50%,#2f3a4a)"></div>
</section>

<footer class="footer">
  <div class="wordmark">Reach Crafters</div>
  <div class="fcol" style="left:487px"><h5>Quick Links</h5>
    <ul><li>Home</li><li>About</li><li>Services</li><li>Blog</li><li>Contact Us</li></ul></div>
  <div class="fcol" style="left:680px"><h5>Help Links</h5>
    <ul><li>FAQ</li><li>Terms of use</li><li>Privacy Policy</li><li>Support Links</li><li>Conditions</li></ul></div>
  <div class="fcol" style="left:886px"><h5>Contact Us</h5>
    <div style="margin-top:14px">
      <div class="contact-row"><svg width="30" height="30" viewBox="0 0 30 30"><circle cx="15" cy="15" r="15" fill="var(--blue)"/><path d="M15 7a5.5 5.5 0 0 0-5.5 5.5C9.5 17 15 23 15 23s5.5-6 5.5-10.5A5.5 5.5 0 0 0 15 7zm0 7.5a2 2 0 1 1 0-4 2 2 0 0 1 0 4z" fill="#fff"/></svg><span>Reach Crafters<br>United States</span></div>
      <div class="contact-row" style="margin-top:12px"><svg width="30" height="30" viewBox="0 0 30 30"><circle cx="15" cy="15" r="15" fill="var(--blue)"/><path d="M11.5 13.5a9 9 0 0 0 5 5l1.6-1.6c.2-.2.5-.3.8-.2.8.3 1.6.4 2.4.4.4 0 .7.3.7.7v2.5c0 .4-.3.7-.7.7A12 12 0 0 1 9 9.7c0-.4.3-.7.7-.7h2.5c.4 0 .7.3.7.7 0 .8.1 1.6.4 2.4.1.3 0 .6-.2.8z" fill="#fff"/></svg><span>+1 888 888 8888</span></div>
      <div class="contact-row" style="margin-top:14px"><svg width="30" height="30" viewBox="0 0 30 30"><circle cx="15" cy="15" r="15" fill="var(--blue)"/><rect x="8" y="10" width="14" height="10" rx="1.5" fill="#fff"/><path d="M8.5 10.5 15 15.5l6.5-5" fill="none" stroke="var(--blue)" stroke-width="1.5"/></svg><span>info@reachcrafters.com</span></div>
    </div>
  </div>
  <div class="rule"></div>
  <p class="copy">Copyrights@2026.Reach Crafters.All Rights Reserved</p>
</footer>

</body>
</html>
```